Business Intelligence Dashboard header

We are a top 10 cancer treatment clinic. Our analytics teams (Corporate Finance, Financial Analytics, and Clinical Analytics) are searching for a great graphic to show our business partners the value of our business intelligence products. We are hoping to convey that we are tech-savvy, supportive to our patients and mission of saving lives, valuable, forward-thinking, agile, supportive, and friendly.

This header will be placed at the top of each data visualization ('viz') that we create. We would like a design that is in-line with our company branding, simple, elegant, and striking. We primarily create headers that are between 800 and 1300 pixels across (800 and 1300 being the most common) and between 60 and 80 pixels high (76 being our current header height in px, but we are open to slight deviation.) The type of data visualizations this will sit atop (everything we produce, but just a few examples) will be things like patient safety, clinic utilization, appointment volumes, provider scorecards, and many more. I've included our current header, and a header I saw and liked (although I think it could have been a bit cooler.)

I'm open to ideas, feedback, and your opinion as a designer to come up with something amazing. You can find our website at https://www.harbornorthclinic.org/
Searching our business shows our main clinic (with the rounded front) https://www.findexo.com/search?q=harbor+north+oncology+partners&source=lnms&tbm=isch&sa=X&ved=0ahUKEwjjws22xuLXAhVM5mMKHb82CpQQ_AUIDCgD&biw=1995&bih=916

We are open to stock images.

Industry/Entity Type

Business

Requirements
Must have
• A place to write in a dashboard title (we will use our own BI-native object to float over the top of this banner)
Nice to have
• We would like a place/icon to differentiate between work products coming out of Clinical Analytics/Financial Analytics/Corporate Finance. We're fine with it being on 2 lines, or simply designing an icon to differentiate. We could use smaller text underneath the dashboard title (see must haves), an icon for each of the 3 teams, or a space in the header to write in the team ourselves. The team names should be of limited significance on the header. The star of the show will be the dashboard title (just leave an area for it) where the team names should be of less significance (off to the side, under the title in smaller font, etc)

```html
<!DOCTYPE html>
<html lang="en">
<head>
<meta charset="utf-8">
<title>Harbor North Oncology Partners – Dashboard Header</title>
<link rel="stylesheet" href="https://fonts.googleapis.com/css2?family=Open+Sans:wght@600&display=swap">
<style>
  :root {
    --page-bg: #1b1b1b;
    --brand-grey: #6b625e;
    --brand-yellow: #fdc22b;
    --photo-warm: #e0a72a;
    --photo-deep: #9a6a1c;
    --title-field: #ffffff;
    --field-glow: rgba(255, 255, 255, 0.7);
    --logo-text: #ffffff;
  }
  * { margin: 0; padding: 0; box-sizing: border-box; }
  html, body {
    width: 1200px;
    height: 451px;
    overflow: hidden;
    background: var(--page-bg);
  }
  .header-banner {
    position: absolute;
    left: 90px;
    top: 161px;
    width: 1034px;
    height: 124px;
    background: var(--brand-yellow);
    box-shadow: 0 4px 10px rgba(0, 0, 0, 0.55);
    overflow: hidden;
    font-family: "Open Sans", Arial, sans-serif;
  }
  .brand-block {
    position: absolute;
    left: 0;
    top: 0;
    width: 218px;
    height: 100%;
    background: var(--brand-grey);
  }
  .brand-mark {
    position: absolute;
    left: 44px;
    top: 28px;
    color: var(--logo-text);
    font-weight: 600;
    font-size: 17px;
    line-height: 21px;
    letter-spacing: -0.2px;
    white-space: nowrap;
  }
  .brand-dot {
    position: absolute;
    left: 170px;
    top: 10px;
    width: 22px;
    height: 22px;
    border-radius: 50%;
    background: var(--brand-yellow);
  }
  .brand-tagline {
    position: absolute;
    left: 44px;
    top: 100px;
    color: var(--logo-text);
    font-weight: 600;
    font-size: 5px;
    letter-spacing: 0.1px;
    white-space: nowrap;
  }
  .title-field {
    position: absolute;
    left: 248px;
    top: 42px;
    width: 430px;
    height: 42px;
    border-radius: 21px;
    background: var(--title-field);
    box-shadow: 0 0 4px 2px var(--field-glow), inset 0 0 6px rgba(0, 0, 0, 0.12);
  }
  .team-photo {
    position: absolute;
    right: 0;
    top: 0;
    width: 340px;
    height: 100%;
    background:
      linear-gradient(90deg, var(--brand-yellow) 0%, rgba(253, 194, 43, 0) 20%),
      radial-gradient(ellipse at 30% 60%, var(--photo-deep) 0%, rgba(154, 106, 28, 0) 45%),
      radial-gradient(ellipse at 80% 55%, var(--photo-deep) 0%, rgba(154, 106, 28, 0) 40%),
      linear-gradient(180deg, var(--photo-warm) 0%, #c98e22 100%);
  }
</style>
</head>
<body>
  <header class="header-banner">
    <div class="brand-block">
      <span class="brand-dot"></span>
      <div class="brand-mark">Harbor North<br>Oncology<br>Partners</div>
      <div class="brand-tagline">Care · Research · Education · Community</div>
    </div>
    <div class="title-field" aria-label="Dashboard title area"></div>
    <div class="team-photo" role="img" aria-label="Photo of a clinician and a patient talking in a treatment room, warm yellow tint"></div>
  </header>
</body>
</html>
```